Alaska Law Firm Needs a Sticker Design

We need a design for stickers to put on already-printed brochures. We mail the brochures to potential clients so they can learn more about accident-induced injuries, insurance claims, legal representation, and our own law firm.

One of our lawyers wrote a book that provides a helpful overview of personal injury claims. We are offering this book for free to anyone who calls and requests it. Therefore, the sticker design should include one of the following phrases, or something very similar:
a) "Still have questions? Call and request our book-- for free!"
b) "Still have questions about auto accident claims? Call and request our book today."
c) "Still have questions about filing a claim? Call and request a free copy of our book."
d) "Still have questions? Call us today to request a free copy of our book, Clear Lanes Ahead."
e) "To learn more about automobile accidents and insurance, call today and request a free copy of our book."

The sticker should be approximately 3"x3" and may be a circle, square, rectangle, or ellipsis. The sticker will be placed on the back of the folder, which is light blue. We would like the sticker to match the color scheme of our website and the folder.

I will upload an image of the book cover as soon as I obtain it.

Law Firm

Font styles to use
Serif
Sans Serif

Requirements
Should not have
• Bright colors that aren't already used in the folder design. e.g. no bright orange, pink, chartreuse, turquoise, yellow, red.

```html
<!DOCTYPE html>
<html lang="en">
<head>
<meta charset="utf-8">
<title>Sticker Designs – Clear Lanes Ahead</title>
<link rel="stylesheet" href="https://fonts.googleapis.com/css2?family=Oswald:wght@600&family=Arimo:ital,wght@0,400;0,700;1,400;1,700&family=Stardos+Stencil:wght@700&display=swap">
<style>
  :root {
    --page: #ffffff;
    --frame: #9a9a9a;
    --blue-deep: #0c3b63;
    --blue-mid: #1a5d92;
    --blue-glow: #3a8ccb;
    --band: #4a4a50;
    --band-edge: #8a8b91;
    --white: #ffffff;
    --cover-a: #7a9fc4;
    --cover-b: #3f6e3a;
  }
  * { box-sizing: border-box; margin: 0; padding: 0; }
  html, body { width: 1200px; height: 801px; overflow: hidden; background: var(--page); }
  .sheet {
    position: relative; width: 1200px; height: 801px;
    border: 1px solid var(--frame); background: var(--page);
  }
  .sticker {
    position: absolute; width: 342px; height: 342px; border-radius: 13px; overflow: hidden;
    background: radial-gradient(ellipse 70% 60% at 50% 78%, var(--blue-glow) 0%, var(--blue-mid) 45%, var(--blue-deep) 100%);
    color: var(--white); font-family: "Arimo", Arial, sans-serif; text-align: center;
  }
  .col-1 { left: 29px; } .col-2 { left: 429px; } .col-3 { left: 828px; }
  .row-1 { top: 29px; } .row-2 { top: 429px; }
  .lead { position: absolute; left: 0; right: 0; font-size: 21px; line-height: 26px; }
  .headline {
    position: absolute; left: 0; right: 0; font-family: "Oswald", "Arial Narrow", sans-serif;
    font-weight: 600; font-size: 40px; line-height: 48px;
  }
  .art { position: absolute; }
  .band {
    position: absolute; left: 0; right: 0; bottom: 0; height: 72px;
    background: var(--band); border-top: 2px solid var(--band-edge); text-align: left;
  }
  .band-tall { height: 72px; }
  .cta-top { position: absolute; left: 25px; top: 5px; font-weight: 700; font-size: 17.5px; }
  .cta-main { position: absolute; left: 25px; top: 28px; font-size: 23px; font-style: italic; }
  .cta-main b { font-weight: 700; }
  .cta-small { position: absolute; left: 25px; font-size: 16px; line-height: 21px; }
  .cta-small em { font-weight: 700; }
  .swoosh { position: absolute; }
  .book {
    position: absolute; right: 22px; bottom: 18px; width: 60px; height: 86px;
    transform: rotate(8deg); border: 2px solid var(--white);
    background: linear-gradient(180deg, var(--cover-a) 0%, #b9c9a8 55%, var(--cover-b) 100%);
    box-shadow: 2px 3px 6px rgba(0,0,0,.45);
  }
  .stamp {
    position: absolute; left: 64px; top: 111px; width: 214px; height: 76px;
    border: 3px solid var(--white); transform: rotate(-4deg);
    font-family: "Stardos Stencil", Georgia, serif; font-weight: 700; font-size: 44px;
    line-height: 70px; letter-spacing: 1px;
  }
</style>
</head>
<body>
<main class="sheet">

  <!-- Sticker 1 -->
  <section class="sticker col-1 row-1">
    <p class="lead" style="top:52px">Still Have</p>
    <h2 class="headline" style="top:70px">Questions</h2>
    <svg class="art" style="left:114px;top:129px" width="114" height="114" viewBox="0 0 114 114" aria-hidden="true">
      <circle cx="57" cy="57" r="56" fill="#fff"/>
      <text x="57" y="88" text-anchor="middle" font-family="Oswald, sans-serif" font-weight="600" font-size="88" fill="#1a5d92">?</text>
    </svg>
    <div class="band">
      <p class="cta-top">Call And Request Our</p>
      <p class="cta-main"><b>BOOK</b> for <b>FREE!</b></p>
      <svg class="swoosh" style="left:200px;top:20px" width="64" height="36" viewBox="0 0 64 36" aria-hidden="true">
        <path d="M2 34 Q30 30 52 8" stroke="#fff" stroke-width="2.5" fill="none"/>
        <path d="M44 6 L58 2 L55 16 Z" fill="#fff"/>
      </svg>
    </div>
    <div class="book" role="img" aria-label="Cover of the book Clear Lanes Ahead"></div>
  </section>

  <!-- Sticker 2 -->
  <section class="sticker col-2 row-1">
    <p class="lead" style="top:17px">Still Have Questions<br>About Auto Accident</p>
    <h2 class="headline" style="top:70px">Claims?</h2>
    <div class="art" role="img" aria-label="Illustration of two cars colliding" style="left:61px;top:126px;width:220px;height:108px;border-radius:10px;background:radial-gradient(ellipse at 50% 60%, rgba(255,255,255,.55), rgba(255,255,255,.08) 70%);"></div>
    <div class="band">
      <p class="cta-top">Call And Request Our</p>
      <p class="cta-main"><b>BOOK</b> for <b>FREE!</b></p>
      <svg class="swoosh" style="left:200px;top:20px" width="64" height="36" viewBox="0 0 64 36" aria-hidden="true">
        <path d="M2 34 Q30 30 52 8" stroke="#fff" stroke-width="2.5" fill="none"/>
        <path d="M44 6 L58 2 L55 16 Z" fill="#fff"/>
      </svg>
    </div>
    <div class="book" role="img" aria-label="Cover of the book Clear Lanes Ahead"></div>
  </section>

  <!-- Sticker 3 -->
  <section class="sticker col-3 row-1">
    <p class="lead" style="top:17px">Still Have Questions<br>About Filing a</p>
    <h2 class="headline" style="top:70px">Claims?</h2>
    <div class="art" role="img" aria-label="Illustration of a document with a pencil" style="left:122px;top:126px;width:146px;height:124px;border-radius:6px;background:linear-gradient(135deg, rgba(255,255,255,.85), rgba(200,200,200,.45));"></div>
    <div class="band">
      <p class="cta-top">Call And Request Our</p>
      <p class="cta-main"><b>BOOK</b> for <b>FREE!</b></p>
      <svg class="swoosh" style="left:200px;top:20px" width="64" height="36" viewBox="0 0 64 36" aria-hidden="true">
        <path d="M2 34 Q30 30 52 8" stroke="#fff" stroke-width="2.5" fill="none"/>
        <path d="M44 6 L58 2 L55 16 Z" fill="#fff"/>
      </svg>
    </div>
    <div class="book" role="img" aria-label="Cover of the book Clear Lanes Ahead"></div>
  </section>

  <!-- Sticker 4 -->
  <section class="sticker col-1 row-2">
    <p class="lead" style="top:52px">Still Have</p>
    <h2 class="headline" style="top:70px">Questions</h2>
    <svg class="art" style="left:114px;top:129px" width="114" height="114" viewBox="0 0 114 114" aria-hidden="true">
      <circle cx="57" cy="57" r="56" fill="#fff"/>
      <text x="57" y="88" text-anchor="middle" font-family="Oswald, sans-serif" font-weight="600" font-size="88" fill="#1a5d92">?</text>
    </svg>
    <div class="band" style="height:92px">
      <p class="cta-small" style="top:2px">Call Us Today To Request</p>
      <p class="cta-small" style="top:24px;font-style:italic"><em>A FREE COPY</em> Of Our <em>BOOK</em>,</p>
      <p class="cta-small" style="top:46px">Clear Lanes Ahead.</p>
      <svg class="swoosh" style="left:172px;top:42px" width="100" height="30" viewBox="0 0 100 30" aria-hidden="true">
        <path d="M2 24 Q50 28 86 14" stroke="#fff" stroke-width="2.5" fill="none"/>
        <path d="M78 8 L96 10 L84 24 Z" fill="#fff"/>
      </svg>
    </div>
    <div class="book" role="img" aria-label="Cover of the book Clear Lanes Ahead" style="bottom:24px"></div>
  </section>

  <!-- Sticker 5 -->
  <section class="sticker col-2 row-2">
    <p class="lead" style="top:17px">To Learn More About<br>Automobile Accidents And</p>
    <h2 class="headline" style="top:71px">Insurance?</h2>
    <div class="art" role="img" aria-label="Illustration of two cars colliding" style="left:73px;top:126px;width:198px;height:114px;border-radius:10px;background:radial-gradient(ellipse at 50% 60%, rgba(255,255,255,.55), rgba(255,255,255,.08) 70%);"></div>
    <div class="band" style="height:75px">
      <p class="cta-top">Call And Request Our</p>
      <p class="cta-main"><b>BOOK</b> for <b>FREE!</b></p>
      <svg class="swoosh" style="left:200px;top:20px" width="64" height="36" viewBox="0 0 64 36" aria-hidden="true">
        <path d="M2 34 Q30 30 52 8" stroke="#fff" stroke-width="2.5" fill="none"/>
        <path d="M44 6 L58 2 L55 16 Z" fill="#fff"/>
      </svg>
    </div>
    <div class="book" role="img" aria-label="Cover of the book Clear Lanes Ahead"></div>
  </section>

  <!-- Sticker 6 -->
  <section class="sticker col-3 row-2">
    <p class="lead" style="top:44px">Still Have Questions<br>About Filing a</p>
    <div class="stamp">CLAIMS?</div>
    <div class="band" style="height:75px">
      <p class="cta-top">Call And Request Our</p>
      <p class="cta-main"><b>BOOK</b> for <b>FREE!</b></p>
      <svg class="swoosh" style="left:200px;top:20px" width="64" height="36" viewBox="0 0 64 36" aria-hidden="true">
        <path d="M2 34 Q30 30 52 8" stroke="#fff" stroke-width="2.5" fill="none"/>
        <path d="M44 6 L58 2 L55 16 Z" fill="#fff"/>
      </svg>
    </div>
    <div class="book" role="img" aria-label="Cover of the book Clear Lanes Ahead"></div>
  </section>

</main>
</body>
</html>
```